Need webdesign for service company that provides Car hiring service and transit service

We need a web design for a company that provides airport transit services and transport services including Limo, Corporate cars, Disability transit, Family transit service. We need is a simple and professional design.

Below is site which we like and also offer the same service http://www.ridelarkway.com.au/
Updates

Project Deadline Extended
Reason: Waiting for the Feedback from multiple stakeholders. Need the time to select and approve the design

Target Market(s)

Tourism, Travel

Industry/Entity Type

Airport

Number of Pages Required

3 page

Font styles to use
Decorative
Script

Requirements
Must have
• Simple and Professional, Site we like http://www.ridelarkway.com.au/ and also need to mobile friendly
Should not have
• Shouldn't have too many images

```html
<!DOCTYPE html>
<html lang="en">
<head>
<meta charset="utf-8">
<title>Ridewell – Private &amp; Business Transport</title>
<link rel="stylesheet" href="https://fonts.googleapis.com/css2?family=Lora:wght@400;700&display=swap">
<style>
:root{
  --ink:#1c1c1c;
  --text:#555;
  --muted:#7a7a7a;
  --white:#fff;
  --icon:#858585;
  --panel:rgba(120,118,122,.82);
  --panel-dark:rgba(105,102,107,.9);
  --btn:#111;
  --rule:#c8c8c8;
  --hero-a:#3a3a40;
  --hero-b:#8f8f98;
  --hero-c:#cfcfd6;
}
*{box-sizing:border-box;margin:0;padding:0}
html,body{width:1186px;height:1200px;overflow:hidden;background:var(--white)}
body{position:relative;font-family:'Lora',Georgia,serif;color:var(--text)}
.site-header{position:absolute;left:0;top:0;width:1186px;height:112px;background:var(--white)}
.brand{position:absolute;left:103px;top:34px;display:flex;align-items:center;gap:12px}
.brand-mark{width:36px;height:36px;border:2px solid var(--ink)}
.brand-name{font-size:30px;font-weight:700;color:var(--ink);letter-spacing:.5px}
.header-tools{position:absolute;left:1000px;top:42px;display:flex;gap:16px}
.header-tools svg{width:20px;height:20px;display:block}
.hero{position:absolute;left:0;top:112px;width:1186px;height:646px;overflow:hidden}
.hero-photo{position:absolute;inset:0;background:linear-gradient(100deg,var(--hero-a) 0%,#4b4b52 28%,var(--hero-b) 45%,var(--hero-c) 70%,#9a9aa2 100%)}
.hero-shade{position:absolute;inset:0;background:rgba(40,40,48,.25)}
.hero-title{position:absolute;left:0;width:100%;top:78px;text-align:center;color:var(--white);font-size:41px;font-weight:700;letter-spacing:1px}
.hero-sub{position:absolute;left:0;width:100%;top:140px;text-align:center;color:var(--white);font-size:22px}
.hero-copy{position:absolute;left:0;width:100%;top:186px;text-align:center;color:var(--white);font-size:12.5px;line-height:21px}
.slider-arrow{position:absolute;top:288px;width:34px;height:50px}
.slider-arrow.prev{left:38px}
.slider-arrow.next{left:1110px}
.card{position:absolute;background:var(--panel);color:var(--white)}
.quote{left:97px;top:292px;width:315px;height:279px;padding:30px 17px}
.quote h2{font-size:19px;font-weight:700;margin-bottom:14px}
.field{display:block;height:29px;border-radius:15px;background:var(--white);color:#444;font-size:11px;font-weight:700;padding:7px 12px;margin-bottom:13px}
.option{display:flex;align-items:center;gap:12px;font-size:12.5px;margin-top:4px;height:27px}
.option svg{width:17px;height:17px}
.btn{display:inline-block;background:var(--btn);color:var(--white);font-size:11px;font-weight:700;border-radius:14px;padding:7px 19px}
.quote .btn{margin-top:11px}
.transit{left:419px;top:292px;width:272px;height:136px;padding:20px 17px}
.transit h3{font-size:14px;font-weight:700}
.transit-icons{display:flex;justify-content:space-between;padding:10px 20px 0 30px}
.driver{left:419px;top:434px;width:272px;height:137px;padding:20px 21px}
.driver h3{font-size:14px;font-weight:400;margin-bottom:14px}
.driver .field{width:194px;height:25px;font-weight:400;padding:5px 10px;font-size:11px;margin-bottom:11px}
.driver .btn{padding:6px 28px}
.corporate{left:698px;top:292px;width:391px;height:279px}
.corporate svg{position:absolute;left:102px;top:60px}
.corporate-label{position:absolute;left:0;bottom:0;width:100%;height:69px;background:var(--panel-dark);font-size:22px;font-weight:700;padding:14px 38px}
.services-title{position:absolute;left:0;width:100%;top:788px;text-align:center;font-size:22px;font-weight:700;color:#3c3c3c}
.service{position:absolute;top:849px;width:200px;text-align:center}
.service-icon{width:120px;height:120px;margin:0 auto;border:2px solid var(--icon);border-radius:50%;display:flex;align-items:center;justify-content:center}
.service h4{font-size:19px;font-weight:400;color:var(--muted);margin-top:20px}
.service p{font-size:12px;line-height:23px;color:var(--muted);margin-top:9px}
.footer-rule{position:absolute;left:97px;top:1127px;width:992px;border-top:1px solid var(--rule)}
.copyright{position:absolute;left:0;width:100%;top:1154px;text-align:center;font-size:12px;color:var(--muted)}
</style>
</head>
<body>
<header class="site-header">
  <div class="brand"><span class="brand-mark"></span><span class="brand-name">RIDEWELL</span></div>
  <nav class="header-tools" aria-label="Tools">
    <svg viewBox="0 0 20 20"><rect x="2" y="3" width="16" height="2.6" fill="#111"/><rect x="2" y="8.7" width="16" height="2.6" fill="#111"/><rect x="2" y="14.4" width="16" height="2.6" fill="#111"/></svg>
    <svg viewBox="0 0 20 20"><path d="M5 2l3 4-2 2c1 2.5 3 4.5 6 6l2-2 4 3-2 3C9 17 3 11 2 5z" fill="#111"/></svg>
    <svg viewBox="0 0 20 20"><circle cx="8.5" cy="8.5" r="5.5" fill="none" stroke="#111" stroke-width="2.6"/><line x1="12.5" y1="12.5" x2="18" y2="18" stroke="#111" stroke-width="3"/></svg>
  </nav>
</header>

<section class="hero">
  <div class="hero-photo" role="img" aria-label="Chauffeur in a dark suit opening the door of a white limousine"></div>
  <div class="hero-shade"></div>
  <h1 class="hero-title">PRIVATE &amp; BUSINESS</h1>
  <p class="hero-sub">Personalised Transport Service</p>
  <p class="hero-copy">Donec et lectus ipsum. Duis vestibulum rutrum finibus. Fusce id sapien sit amet metus volutpat bibendum ut et mi.<br>Vestibulum ante ipsum primis in faucibus orci luctus et ultrices posuere cubilia Curae;</p>
  <svg class="slider-arrow prev" viewBox="0 0 34 50"><polyline points="26,4 8,25 26,46" fill="none" stroke="#ddd" stroke-width="9"/></svg>
  <svg class="slider-arrow next" viewBox="0 0 34 50"><polyline points="8,4 26,25 8,46" fill="none" stroke="#ddd" stroke-width="9"/></svg>

  <form class="card quote">
    <h2>Get Instant Quote</h2>
    <span class="field">Orgin (Public Location or Exact Address)</span>
    <span class="field">Destination (Public Location or Exact Address)</span>
    <div class="option"><svg viewBox="0 0 17 17"><circle cx="8.5" cy="8.5" r="8" fill="#fff"/><path d="M8.5 4v9M4 8.5h9" stroke="#777" stroke-width="2"/></svg>Add Stop</div>
    <div class="option"><svg viewBox="0 0 17 17"><rect x="1" y="4" width="10" height="8" fill="#fff"/><path d="M11 6h3l2 3v3h-5z" fill="#fff"/><circle cx="4" cy="13.5" r="2" fill="#fff"/><circle cx="13" cy="13.5" r="2" fill="#fff"/></svg>Show other Vehicles</div>
    <span class="btn">GET STARTED NOW</span>
  </form>

  <div class="card transit">
    <h3>Family Transit &amp; Disability Transit</h3>
    <div class="transit-icons">
      <svg width="66" height="66" viewBox="0 0 66 66" fill="none" stroke="#fff" stroke-width="2.5"><circle cx="20" cy="12" r="6"/><circle cx="34" cy="10" r="6"/><circle cx="48" cy="12" r="6"/><path d="M10 40V24c0-4 4-6 10-6s10 2 10 6M24 38V22c0-4 4-6 10-6s10 2 10 6v16M38 24c0-4 4-6 10-6s10 2 10 6v14"/><path d="M4 50l14-6h22l22-10-8 14-18 12H4"/></svg>
      <svg width="62" height="76" viewBox="0 0 62 76" fill="none" stroke="#fff" stroke-width="3"><circle cx="24" cy="7" r="5" fill="#fff"/><path d="M24 16v24h20l10 18"/><path d="M24 28h14"/><path d="M14 34a20 20 0 1 0 30 22"/></svg>
    </div>
  </div>

  <form class="card driver">
    <h3>Want to Become a driver</h3>
    <span class="field">Enter your mail...</span>
    <span class="btn">SIGNUP HERE</span>
  </form>

  <div class="card corporate">
    <svg width="186" height="104" viewBox="0 0 186 104" fill="none" stroke="#fff" stroke-width="4"><path d="M4 78V48l48-6 30-34h50l34 32 16 8v30h-28M52 78H138M4 78h18"/><circle cx="37" cy="80" r="16"/><circle cx="153" cy="80" r="16"/></svg>
    <div class="corporate-label">Corporate Cars</div>
  </div>
</section>

<h2 class="services-title">Special Services</h2>

<article class="service" style="left:86px">
  <div class="service-icon"><svg width="96" height="30" viewBox="0 0 96 30" fill="none" stroke="#858585" stroke-width="2"><path d="M2 22V14l16-2 8-8h50l10 8 8 2v8H2z"/><path d="M28 6v8M44 6v8M60 6v8M76 6v8"/><circle cx="18" cy="23" r="5" fill="#fff"/><circle cx="80" cy="23" r="5" fill="#fff"/></svg></div>
  <h4>Limo</h4>
  <p>Duis dignissim est odio, eleifend convallis diam sollicitudin ut</p>
</article>
<article class="service" style="left:290px">
  <div class="service-icon"><svg width="60" height="56" viewBox="0 0 60 56" fill="#858585"><path d="M2 4h30v52H2zM32 18h26v38H32z"/><g fill="#fff"><rect x="7" y="9" width="6" height="6"/><rect x="19" y="9" width="6" height="6"/><rect x="7" y="21" width="6" height="6"/><rect x="19" y="21" width="6" height="6"/><rect x="7" y="33" width="6" height="6"/><rect x="19" y="33" width="6" height="6"/><rect x="7" y="45" width="6" height="6"/><rect x="19" y="45" width="6" height="6"/><rect x="37" y="24" width="6" height="6"/><rect x="48" y="24" width="6" height="6"/><rect x="37" y="35" width="6" height="6"/><rect x="48" y="35" width="6" height="6"/><rect x="37" y="46" width="6" height="6"/><rect x="48" y="46" width="6" height="6"/></g></svg></div>
  <h4>Corporate cars</h4>
  <p>Duis dignissim est odio, eleifend convallis diam sollicitudin ut</p>
</article>
<article class="service" style="left:493px">
  <div class="service-icon"><svg width="60" height="64" viewBox="0 0 60 64" fill="none" stroke="#858585" stroke-width="2"><circle cx="10" cy="6" r="4"/><path d="M4 14h12v24h-3v24H7V38H4z"/><path d="M16 26h12"/><circle cx="38" cy="12" r="4"/><path d="M34 20v20h14l6 14h4M34 30h10"/><circle cx="34" cy="52" r="10"/></svg></div>
  <h4>Disability Transit</h4>
  <p>Duis dignissim est odio, eleifend convallis diam sollicitudin ut</p>
</article>
<article class="service" style="left:696px">
  <div class="service-icon"><svg width="70" height="60" viewBox="0 0 70 60" fill="#858585"><circle cx="12" cy="5" r="5"/><path d="M4 12h16v22h-3v24h-4V36h-2v22H7V34H4z"/><circle cx="34" cy="5" r="5"/><path d="M27 12h14l5 26h-6v20h-3V38h-2v20h-3V38h-6z"/><circle cx="58" cy="20" r="4"/><path d="M52 26h12v16h-2v16h-3V44h-2v14h-3V42h-2z"/></svg></div>
  <h4>Family transit</h4>
  <p>Duis dignissim est odio, eleifend convallis diam sollicitudin ut</p>
</article>
<article class="service" style="left:899px">
  <div class="service-icon"><svg width="62" height="62" viewBox="0 0 62 62" fill="none" stroke="#858585" stroke-width="2.5"><path d="M52 22A26 26 0 1 0 50 46"/><path d="M28 14v18l8 6"/><path d="M60 40H42M48 34l-6 6 6 6"/></svg></div>
  <h4>Real time booking</h4>
  <p>Duis dignissim est odio, eleifend convallis diam sollicitudin ut</p>
</article>

<div class="footer-rule"></div>
<footer class="copyright">© Copyright 2017 - Ridewell - Allrights Reserved.</footer>
</body>
</html>
```